Moravel Aesthetic Doctor

I require an elegant, luxurious looking business card for my aesthetic business. I am a doctor and that will set me aside from competitors. I am planning to provide home and spa based treatments to clients with high expectations. I have attached my logo.

```html
<!DOCTYPE html>
<html lang="en">
<head>
<meta charset="utf-8">
<title>Moravel Aesthetic Doctor – Business Card</title>
<link href="https://fonts.googleapis.com/css2?family=Arimo:wght@400;700&display=swap" rel="stylesheet">
<style>
  :root {
    --backdrop: #1c1c1c;
    --blue-deep: #0f76cc;
    --blue-mid: #2a8fd8;
    --blue-light: #4fb2e4;
    --sky-band: #7ecbec;
    --grey-band: #a7a9ac;
    --logo-grey: #9d9fa2;
    --white: #ffffff;
  }
  * { box-sizing: border-box; margin: 0; padding: 0; }
  html, body {
    width: 1093px; height: 1200px; overflow: hidden;
    background: var(--backdrop);
    font-family: "Arimo", Arial, sans-serif;
  }
  .card {
    position: absolute; left: 264px; width: 580px; height: 357px;
    overflow: hidden;
    box-shadow: 0 4px 10px rgba(0,0,0,.6);
  }
  .card--front { top: 226px; color: var(--white); text-align: center; }
  .card--back { top: 620px; background: var(--white); }
  .front-backdrop {
    position: absolute; inset: 0;
    background: linear-gradient(160deg, var(--blue-mid) 0%, var(--blue-deep) 50%, var(--blue-light) 100%);
  }
  .front-content { position: relative; height: 100%; }
  .doctor-name { position: absolute; top: 74px; width: 100%; font-size: 24px; font-weight: 700; }
  .doctor-name .credentials { font-size: 14px; font-weight: 400; }
  .qualification { position: absolute; top: 102px; width: 100%; font-size: 17px; font-weight: 400; }
  .divider-row {
    position: absolute; width: 100%; display: flex; justify-content: center; align-items: center; gap: 4px;
  }
  .divider-row .rule { width: 50px; height: 1px; background: rgba(255,255,255,.7); margin: 0 2px; }
  .contact-icons { top: 137px; }
  .contact-icon {
    width: 24px; height: 24px; background: var(--white); border-radius: 3px;
    display: flex; align-items: center; justify-content: center;
  }
  .contact-lines { position: absolute; top: 175px; width: 100%; font-size: 16.5px; line-height: 21px; }
  .social-icons { top: 249px; }
  .social-icons .rule { width: 55px; }
  .social-circle { width: 30px; height: 30px; border: 1.6px solid var(--white); border-radius: 50%; }

  .brand { position: absolute; top: 66px; left: 108px; display: flex; align-items: center; gap: 14px; }
  .brand-circle { width: 104px; height: 104px; border: 2.5px solid var(--logo-grey); border-radius: 50%; }
  .brand-name { color: var(--logo-grey); font-weight: 400; line-height: 1; }
  .brand-name .word { display: block; font-size: 45px; letter-spacing: 2px; }
  .brand-name .tagline { display: block; font-size: 19px; letter-spacing: 1px; margin-top: 8px; }
  .band-title {
    position: absolute; top: 202px; left: 0; width: 100%; height: 39px;
    background: var(--grey-band); color: var(--white);
    font-size: 17.5px; text-align: center; line-height: 39px;
  }
  .band-services {
    position: absolute; top: 245px; left: 0; width: 100%; height: 62px;
    background: var(--sky-band); color: var(--white);
    font-size: 17.5px; text-align: center; line-height: 21px; padding-top: 9px;
  }
  .dot { display: inline-block; width: 7px; height: 7px; background: var(--white); border-radius: 50%; margin: 0 10px; vertical-align: middle; }
</style>
</head>
<body>

<section class="card card--front">
  <div class="front-backdrop" role="img" aria-label="Flowing blue wave pattern background"></div>
  <div class="front-content">
    <h1 class="doctor-name">Dr Elena Varga <span class="credentials">MRCPCH MD</span></h1>
    <p class="qualification">Australasian Diploma of Aesthetic Medicine</p>

    <div class="divider-row contact-icons">
      <span class="rule"></span>
      <span class="contact-icon" aria-label="Phone">
        <svg width="16" height="14" viewBox="0 0 16 14"><path d="M1 5 C1 1 15 1 15 5 L12 6 L11 4 H5 L4 6Z M4 7 H12 L14 13 H2Z" fill="var(--blue-deep)"/></svg>
      </span>
      <span class="contact-icon" aria-label="Email">
        <svg width="16" height="12" viewBox="0 0 16 12"><rect x="1" y="1" width="14" height="10" fill="none" stroke="var(--blue-deep)" stroke-width="1.4"/><path d="M1 1 L8 7 L15 1 M1 11 L6 6 M15 11 L10 6" stroke="var(--blue-deep)" stroke-width="1.2" fill="none"/></svg>
      </span>
      <span class="contact-icon" aria-label="Website">
        <svg width="16" height="16" viewBox="0 0 16 16"><circle cx="8" cy="8" r="7" fill="var(--blue-deep)"/><path d="M5 4 C7 5 6 7 8 8 C9 10 7 12 8 14 M10 3 C11 5 13 5 14 7" stroke="var(--white)" stroke-width="1.4" fill="none"/></svg>
      </span>
      <span class="rule"></span>
    </div>

    <p class="contact-lines">0800 555 019<br>elena@moravel.co.nz<br>www.moravel.co.nz</p>

    <div class="divider-row social-icons">
      <span class="rule"></span>
      <span class="social-circle" aria-label="Social profile"></span>
      <span class="social-circle" aria-label="Social profile"></span>
      <span class="rule"></span>
    </div>
  </div>
</section>

<section class="card card--back">
  <div class="brand">
    <span class="brand-circle"></span>
    <p class="brand-name"><span class="word">MORAVEL</span><span class="tagline">AESTHETIC DOCTOR</span></p>
  </div>
  <p class="band-title">HOME AND SPA BASED TREATMENTS</p>
  <p class="band-services">
    Dermal injectables<span class="dot"></span>Plasma facials<span class="dot"></span>Microneedling<br>
    Skin boosters<span class="dot"></span>Excessive sweating
  </p>
</section>

</body>
</html>
```